business card deign

Logo needs the following on it.
1. attached logo
2. Tagline - "If it keeps a drink cold or the party going...we do it!"
3. Name- Dalton Pikes, Founder and CPO
4. Address - 412 E. Carver Avenue, Ste 2207, Tampa, FL. 33917
5. Phone - 555.318.4726

```html
<!DOCTYPE html>
<html lang="en">
<head>
<meta charset="utf-8">
<title>Kipara Business Card</title>
<link href="https://fonts.googleapis.com/css2?family=Cabin:wght@600;700&family=League+Spartan:wght@900&family=Roboto:wght@300;400;500&family=Roboto+Condensed:wght@500&display=swap" rel="stylesheet">
<style>
  :root {
    --stage: #737373;
    --card-dark-top: #2b2b2b;
    --card-dark-bottom: #050505;
    --card-light: #ffffff;
    --ink: #1a1a1a;
    --ink-soft: #2c2c2c;
    --white: #ffffff;
    --rule: #3a3a3a;
    --mark-dark: rgba(255,255,255,0.05);
    --mark-light: rgba(0,0,0,0.045);
  }
  * { margin: 0; padding: 0; box-sizing: border-box; }
  html, body { width: 1200px; height: 1000px; overflow: hidden; }
  body { background: var(--stage); position: relative; font-family: "Roboto", sans-serif; }

  .card {
    position: absolute;
    left: 294px;
    width: 612px;
    height: 351px;
    border-radius: 22px;
    overflow: hidden;
  }
  .card--front {
    top: 103px;
    background: linear-gradient(160deg, var(--card-dark-top) 0%, #141414 45%, var(--card-dark-bottom) 100%);
  }
  .card--back {
    top: 507px;
    background: var(--card-light);
    box-shadow: 0 14px 30px rgba(0,0,0,0.35);
  }

  .brand-decoration {
    position: absolute;
    right: 0;
    top: 0;
    width: 290px;
    height: 351px;
  }
  .card--front .brand-decoration {
    background: radial-gradient(ellipse at 70% 45%, var(--mark-dark) 0%, rgba(255,255,255,0) 70%);
  }
  .card--back .brand-decoration {
    background: radial-gradient(ellipse at 65% 50%, var(--mark-light) 0%, rgba(0,0,0,0) 70%);
  }

  .tagline {
    position: absolute;
    left: 0;
    width: 100%;
    text-align: center;
    color: var(--white);
  }
  .tagline__lead {
    top: 126px;
    left: 107px;
    width: auto;
    font-family: "Cabin", sans-serif;
    font-weight: 700;
    font-size: 19px;
    letter-spacing: 0.1px;
  }
  .tagline__punch {
    top: 148px;
    left: 86px;
    width: auto;
    font-family: "League Spartan", sans-serif;
    font-weight: 900;
    font-size: 82px;
    letter-spacing: 1px;
    line-height: 1;
  }

  .wordmark {
    position: absolute;
    left: 34px;
    top: 110px;
    font-family: "Roboto Condensed", sans-serif;
    font-weight: 500;
    font-size: 18px;
    letter-spacing: 6.4px;
    color: var(--ink);
  }

  .person {
    position: absolute;
    left: 33px;
    top: 234px;
    color: var(--ink);
  }
  .person__name {
    font-weight: 500;
    font-size: 15px;
    letter-spacing: 0.4px;
    line-height: 18px;
  }
  .person__title {
    font-weight: 300;
    font-size: 15px;
    line-height: 20px;
  }

  .divider {
    position: absolute;
    left: 33px;
    top: 286px;
    width: 547px;
    height: 1px;
    background: var(--rule);
  }

  .contact {
    position: absolute;
    top: 301px;
    font-weight: 300;
    font-size: 15px;
    color: var(--ink-soft);
    line-height: 20px;
  }
  .contact--phone { left: 33px; display: flex; align-items: center; gap: 4px; }
  .contact--phone svg { width: 10px; height: 10px; }
  .contact--address { right: 32px; text-align: right; }
</style>
</head>
<body>

  <section class="card card--front" aria-label="Card front">
    <div class="brand-decoration" role="img" aria-label="Faint large brand mark decoration"></div>
    <p class="tagline tagline__lead">If it keeps a drink cold or the party going...</p>
    <p class="tagline tagline__punch">WE DO IT!</p>
  </section>

  <section class="card card--back" aria-label="Card back">
    <div class="brand-decoration" role="img" aria-label="Faint large brand mark decoration"></div>
    <p class="wordmark">KIPARA</p>

    <div class="person">
      <p class="person__name">DALTON PIKES</p>
      <p class="person__title">Founder and CPO</p>
    </div>

    <div class="divider"></div>

    <p class="contact contact--phone">
      <svg viewBox="0 0 24 24" aria-hidden="true"><path fill="#1a1a1a" d="M6.6 10.8a15.1 15.1 0 0 0 6.6 6.6l2.2-2.2c.3-.3.7-.4 1-.2 1.1.4 2.3.6 3.6.6.6 0 1 .4 1 1V20c0 .6-.4 1-1 1A17 17 0 0 1 3 4c0-.6.4-1 1-1h3.5c.6 0 1 .4 1 1 0 1.3.2 2.5.6 3.6.1.3 0 .7-.2 1z"/></svg>
      555.318.4726
    </p>
    <p class="contact contact--address">412 E. Carver Avenue, Ste 2207, Tampa, FL. 33917</p>
  </section>

</body>
</html>
```